Modernize Website: marcusfellwright.net

I am a novelist with an older-generation website at: marcusfellwright.net.

I am hoping to refresh this outdated website with a new, responsive redesign. I would prefer to host the code myself, and edit using Adobe Dreamweaver. So I’m not looking to use a hosted site builder like Plexo. Nor am I looking to use a CMS like Pagecraft.

In order to simplify the old site, there are a number of sections I’ll be looking to remove during this redesign. These are shown in the "MF Site Redesign" attachment. I can also provide imagery for new content (another book series in addition to the existing one), as well as higher-resolution imagery (if needed) of the old content.

Happy to answer any further questions.
Updates

I've uploaded a ZIP file containing high-res artwork associated with the new trilogy of books.

Target Market(s)

Readers of epic fantasy novels such as H.W.B. Castellane's THE WARDEN OF THE VALES, Harold P.Q. Ventris's A CROWN OF ASH AND RAIN, Victor Halloway's THE GATE OF STARS, or Dennis Vale's BLADE OF MERIVANE.

Industry/Entity Type

Entertainment

Coding

Coded - Design and coding required

Number of Pages Required

5+ page

Font styles to use
Serif
Decorative

Colors

Designer to choose colors to be used in the design.

Requirements
Must have
• I'm looking for a responsive design that displays nicely on both mobile and desktop devices. Existing site contains multiple pages, but these can obviously be combined into fewer pages (or even one) by divisions such as tabs, sections, and/or modal windows. See marcusfellwright.net for current content and "MF Site Redesign" attachment for content to be removed at this time.
Nice to have
• The ability to fulfill orders of autographed books directly from the website. I currently use Coinlo to do this, but it would be nice to incorporate a more comprehensive merchant service at a reasonable rate.
Should not have
• I'd like to host and control the site code myself. So please don't use a hosted web builder like Plexo, or a cloud-based CMS like Pagecraft.

```html
<!DOCTYPE html>
<html lang="en">
<head>
<meta charset="utf-8">
<title>Marcus Fellwright — Author</title>
<link href="https://fonts.googleapis.com/css2?family=Cinzel:wght@400;700&family=Cinzel+Decorative:wght@700&family=Open+Sans:wght@400;600&display=swap" rel="stylesheet">
<style>
:root{
  --bg:#151b25;
  --bg-deep:#0d1118;
  --band:#0a0d12;
  --ink:#e9ecef;
  --muted:#c4cad2;
  --red:#e3141b;
  --steel-hi:#f2f4f6;
  --steel-lo:#8e97a2;
  --steel-dark:#2b323c;
  --glow:#3f7fb8;
  --line:#6e7782;
}
*{margin:0;padding:0;box-sizing:border-box}
html,body{width:1200px;height:3291px;overflow:hidden}
body{
  position:relative;
  background:
    radial-gradient(ellipse 700px 500px at 600px 1150px,#2a3442 0%,transparent 70%),
    radial-gradient(ellipse 800px 600px at 600px 400px,#222b38 0%,transparent 70%),
    radial-gradient(ellipse 700px 400px at 600px 2050px,#1f2733 0%,transparent 70%),
    var(--bg);
  color:var(--ink);
  font-family:"Open Sans",sans-serif;
}
.abs{position:absolute}

/* header */
.brand{left:99px;top:14px;font-family:"Cinzel",serif;font-size:28px;line-height:34px;color:var(--muted);letter-spacing:1px}
.main-nav{left:590px;top:30px;display:flex;gap:6px}
.main-nav a{display:block;width:130px;height:52px;line-height:52px;text-align:center;
  font-family:"Open Sans",sans-serif;font-weight:600;font-size:13px;color:var(--ink);text-decoration:none;
  background:linear-gradient(#262c35,#10141a);border:2px solid #3a424d;border-radius:8px;text-transform:uppercase}
.main-nav a.is-active{border-color:var(--glow);box-shadow:0 0 10px var(--glow)}

/* hero */
.hero{left:114px;top:121px;width:972px;height:548px;
  background:radial-gradient(ellipse 500px 320px at 250px 200px,#7d8286 0%,#4a5159 45%,#262d37 100%);
  box-shadow:0 0 30px #000}
.hero-title{left:149px;top:272px;font-family:"Cinzel",serif;font-size:55px;line-height:60px;color:#fff;font-weight:400}
.hero-tagline{left:149px;top:419px;font-weight:600;font-size:19px;color:#fff}
.hero-books{left:544px;top:208px;width:476px;height:389px;
  background:linear-gradient(100deg,#6b4c55 0%,#b4552d 35%,#d9782e 60%,#8a2d1a 100%)}
.hero-arrow{top:355px;width:38px;height:79px;background:linear-gradient(#e8eaec,#9da4ad);border-radius:3px}
.hero-arrow svg{display:block;margin:27px auto 0}

/* buttons */
.btn{display:block;height:36px;line-height:36px;text-align:center;font-family:"Cinzel",serif;font-weight:700;
  font-size:13px;color:#1b1f25;background:linear-gradient(var(--steel-hi),var(--steel-lo));
  border:2px solid var(--steel-dark);border-radius:3px;box-shadow:0 0 12px rgba(63,127,184,.55)}

/* section banners */
.banner{left:175px;width:850px;height:100px}
.banner svg{position:absolute;inset:0}
.banner h2{position:absolute;inset:0;text-align:center;line-height:100px;font-family:"Cinzel Decorative",serif;
  font-size:44px;color:var(--red);letter-spacing:2px}

/* tabs */
.tab{font-family:"Cinzel",serif;font-weight:700;font-size:19px;color:var(--ink)}
.tab-active{height:40px;line-height:36px;text-align:center;font-size:17px;color:#1b1f25;
  background:linear-gradient(var(--steel-hi),var(--steel-lo));border:2px solid var(--steel-dark);
  box-shadow:0 0 14px rgba(63,127,184,.7)}

/* novels */
.book{width:300px;text-align:center}
.book-cover{width:149px;height:224px;margin:0 auto;border:2px solid #9aa1aa}
.book-title{margin-top:28px;font-family:"Cinzel",serif;font-weight:700;font-size:19px;letter-spacing:1px}
.book-series{margin-top:8px;font-size:14px;line-height:22px;color:var(--muted)}
.book .btn{width:146px;margin:18px auto 0}

.band{left:0;width:1200px;height:40px;background:var(--band);border-top:1px solid #2c333d;border-bottom:1px solid #2c333d}

/* world */
.note{left:0;width:1200px;text-align:center;font-size:15px;line-height:33px;color:var(--ink)}
.map{width:257px;height:279px}
.ornament-blade{width:108px;height:16px;background:linear-gradient(90deg,#d8dde3,#b5151a 40%,#e02a22 70%,#d8dde3)}

/* author */
.bio{left:99px;width:774px;font-size:14.5px;line-height:27px;color:var(--ink)}
.bio p+p{margin-top:14px}
.portrait{left:908px;top:2716px;width:191px;height:257px;border:3px solid #b7bdc4;
  background:linear-gradient(160deg,#6f5a52,#2d2a2c 60%,#161618)}

/* footer */
.rule{height:1px;background:var(--line)}
.footer-nav{left:0;width:1200px;top:3142px;text-align:center;font-weight:600;font-size:15px}
.footer-nav a{color:var(--ink);text-decoration:none;margin:0 44px}
.footer-nav span{color:var(--ink)}
.copyright{left:99px;top:3238px;font-size:14px}
.social{left:880px;top:3232px;display:flex;gap:14px;font-size:13px}
.social li{list-style:none;display:flex;align-items:center;gap:5px}
.social li::before{content:"";width:14px;height:14px;border:2px solid var(--ink);border-radius:50%}
</style>
</head>
<body>

<header>
  <div class="abs brand">Marcus<br>Fellwright</div>
  <nav class="abs main-nav">
    <a class="is-active" href="#home">Home</a>
    <a href="#novels">Novels</a>
    <a href="#author">Author</a>
    <a href="#world">World</a>
  </nav>
</header>

<section id="home">
  <div class="abs hero"></div>
  <div class="abs hero-books" role="img" aria-label="Covers of the three Saga of Veloran novels fanned out"></div>
  <h1 class="abs hero-title">MARCUS<br>FELLWRIGHT</h1>
  <p class="abs hero-tagline">Plenty Of Violence And Magical Mayhem</p>
  <a class="abs btn" style="left:149px;top:489px;width:147px" href="#novels">Read More</a>
  <div class="abs hero-arrow" style="left:44px"><svg width="16" height="24"><path d="M13 2 3 12l10 10" fill="none" stroke="#111" stroke-width="4"/></svg></div>
  <div class="abs hero-arrow" style="left:1125px"><svg width="16" height="24"><path d="M3 2l10 10L3 22" fill="none" stroke="#111" stroke-width="4"/></svg></div>
</section>

<section id="novels">
  <div class="abs banner" style="top:746px">
    <svg viewBox="0 0 850 100" width="850" height="100"><path d="M0 50 110 18h630l110 32-110 32H110Z" fill="#1b2129" stroke="#8a939e" stroke-width="2"/><path d="M120 28h610v44H120Z" fill="#0c0f14" stroke="#3f7fb8" stroke-width="1"/></svg>
    <h2>NOVELS</h2>
  </div>
  <div class="abs tab tab-active" style="left:248px;top:912px;width:162px">SUMMARIES</div>
  <div class="abs tab" style="left:437px;top:920px">EXCERPTS</div>
  <div class="abs tab" style="left:570px;top:920px">REVIEWS</div>
  <div class="abs tab" style="left:689px;top:920px">BUY ONLINE</div>
  <div class="abs tab" style="left:845px;top:920px">SIGNED COPIES</div>

  <article class="abs book" style="left:109px;top:1016px">
    <div class="book-cover" role="img" aria-label="Cover of The Scarlet Blade" style="background:linear-gradient(160deg,#6e6470,#3e3240 50%,#7a2a33)"></div>
    <h3 class="book-title">THE SCARLET BLADE</h3>
    <p class="book-series">Book One of The Saga of<br>Veloran</p>
    <a class="btn" href="#">Read More</a>
  </article>
  <article class="abs book" style="left:447px;top:1016px">
    <div class="book-cover" role="img" aria-label="Cover of The Onyx Gate" style="background:linear-gradient(160deg,#e0a23a,#b8452a 50%,#4a1c16)"></div>
    <h3 class="book-title">THE ONYX GATE</h3>
    <p class="book-series">Book Two of The Saga of<br>Veloran</p>
    <a class="btn" href="#">Read More</a>
  </article>
  <article class="abs book" style="left:791px;top:1016px">
    <div class="book-cover" role="img" aria-label="Cover of The Sacred Amulet" style="background:linear-gradient(160deg,#2c4a5a,#c45a26 55%,#5a1e12)"></div>
    <h3 class="book-title">THE SACRED AMULET</h3>
    <p class="book-series">Book Three of The Saga of<br>Veloran</p>
    <a class="btn" href="#">Read More</a>
  </article>
</section>

<div class="abs band" style="top:1470px"></div>

<section id="world">
  <div class="abs banner" style="top:1573px">
    <svg viewBox="0 0 850 100" width="850" height="100"><path d="M0 50 110 18h630l110 32-110 32H110Z" fill="#1b2129" stroke="#8a939e" stroke-width="2"/><path d="M120 28h610v44H120Z" fill="#0c0f14" stroke="#3f7fb8" stroke-width="1"/></svg>
    <h2>WORLD</h2>
  </div>
  <div class="abs tab tab-active" style="left:314px;top:1753px;width:162px">MAPS</div>
  <div class="abs tab" style="left:513px;top:1761px">CHARACTERS</div>
  <div class="abs tab" style="left:671px;top:1761px">LOCATIONS</div>
  <div class="abs tab" style="left:816px;top:1761px">ARTIFACTS</div>

  <p class="abs note" style="top:1827px">Below is a pair of maps showing the lands of Morvania and Threlmoor, as featured in The Saga of Veloran.<br>Note: To view a map in full size, click on its thumbnail below.</p>

  <div class="abs map" role="img" aria-label="Map of Threlmoor" style="left:318px;top:1931px;background:linear-gradient(160deg,#27476e,#7a6a4c 45%,#3c5a2e 75%,#27476e)"></div>
  <div class="abs map" role="img" aria-label="Map of Morvania" style="left:630px;top:1931px;background:linear-gradient(200deg,#27476e,#4d6a36 40%,#8a7450 65%,#27476e)"></div>

  <div class="abs ornament-blade" role="img" aria-label="Sword ornament" style="left:138px;top:2261px"></div>
  <p class="abs note" style="top:2253px;font-size:14px">Graphic sketches rendered using the Lords of Rune and Realm Map Builder by Kestrel Soft.</p>
  <div class="abs ornament-blade" role="img" aria-label="Sword ornament" style="left:954px;top:2261px"></div>
</section>

<div class="abs band" style="top:2348px"></div>

<section id="author">
  <div class="abs banner" style="top:2446px">
    <svg viewBox="0 0 850 100" width="850" height="100"><path d="M0 50 110 18h630l110 32-110 32H110Z" fill="#1b2129" stroke="#8a939e" stroke-width="2"/><path d="M120 28h610v44H120Z" fill="#0c0f14" stroke="#3f7fb8" stroke-width="1"/></svg>
    <h2>AUTHOR</h2>
  </div>
  <div class="abs tab tab-active" style="left:268px;top:2615px;width:164px">BIOGRAPHY</div>
  <div class="abs tab" style="left:487px;top:2623px">PHOTOS</div>
  <div class="abs tab" style="left:606px;top:2623px">INFLUENCES</div>
  <div class="abs tab" style="left:761px;top:2623px">ACKNOWLEDGMENTS</div>

  <div class="abs bio" style="top:2704px">
    <p>Weaned on the likes of The Warden of the Vales and Comet Legions, Marcus took to writing fantasy adventure, it seems, almost as soon as he learned to read. By the time he hit grade school, he was writing 30-page stories in lieu of the two or three pages expected of all students on a monthly basis. When at age nine he read Dennis Vale's The Runestones of Merivane, his goal of becoming a fantasy novelist went from child's ambition to hopeless obsession.</p>
    <p>Yet writing was to be a hobby. Even his parents stressed the importance of a "safe" career path. So when the time came, Marcus accepted a scholarship and went off to college, where among his English, writing, and mythology courses, he studied computers, the health sciences, and worked hard to play football.</p>
  </div>
  <div class="abs portrait" role="img" aria-label="Portrait photograph of the author"></div>
  <a class="abs btn" style="left:114px;top:2975px;width:134px" href="#">Read More</a>
</section>

<footer>
  <div class="abs ornament-blade" role="img" aria-label="Sword ornament" style="left:99px;top:3075px"></div>
  <div class="abs rule" style="left:215px;top:3083px;width:770px"></div>
  <div class="abs ornament-blade" role="img" aria-label="Sword ornament" style="left:993px;top:3075px"></div>
  <nav class="abs footer-nav">
    <a href="#home">HOME</a><span>|</span><a href="#novels">NOVELS</a><span>|</span><a href="#world">WORLD</a><span>|</span><a href="#author">AUTHOR</a>
  </nav>
  <div class="abs rule" style="left:99px;top:3203px;width:1002px"></div>
  <p class="abs copyright">Copyrights @ 2018 Marcus Fellwright. All Rights Reserved.</p>
  <ul class="abs social">
    <li>Folio</li><li>Chirp</li><li>Lens</li><li>Orbit</li>
  </ul>
</footer>

</body>
</html>
```